Essential Oil 15ml - package of 6

Design of a box of 6 different essential oils.
+ design of the bottle stickers
My bottles are 15ml clear blue glass.

The pictures attached are my competitors...

Target Market(s)

TERVIK USA

Font styles to use
Serif

Requirements
Must have
• Our logo + "essential oil" and type (lavender, eucalyptus etc....)
• 15ml - 0.50 fl.oz.
• special color for the oil type.

```html
<!DOCTYPE html>
<html lang="en">
<head>
<meta charset="utf-8">
<title>Sela Vale Essential Oil – Labels and Box</title>
<link rel="stylesheet" href="https://fonts.googleapis.com/css2?family=Crimson+Text:wght@400;600&family=Pinyon+Script&display=swap">
<style>
  :root {
    --page: #ffffff;
    --sage-edge: #8db46c;
    --sage-mid: #a9c98a;
    --sage-light: #e6f0cf;
    --lav-edge: #7a4f98;
    --lav-light: #ece2f3;
    --gold: #d9a441;
    --ink: #1c1c1c;
    --white: #ffffff;
    --eucalyptus: #1e2a12;
    --tea-tree: #3f5a2a;
    --peppermint: #c5a5d0;
    --oregano: #94707f;
    --lemon: #e8c414;
    --lavender: #4a2350;
    --box-green: #354a24;
    --box-light: #cfdcaa;
    --measure: #e0302f;
    --board: #eeeeee;
    --serif: "Crimson Text", Georgia, serif;
    --script: "Pinyon Script", cursive;
  }
  html, body { margin: 0; padding: 0; overflow: hidden; }
  body { width: 1200px; height: 1000px; background: var(--page); position: relative; font-family: var(--serif); }

  .label {
    position: absolute; width: 323px; height: 105px; overflow: hidden;
    background: linear-gradient(90deg, var(--sage-edge) 0%, var(--sage-mid) 30%, var(--sage-light) 50%, var(--sage-mid) 70%, var(--sage-edge) 100%);
  }
  .label--lavender {
    background: linear-gradient(90deg, var(--lav-edge) 0%, #b596cc 28%, var(--lav-light) 50%, #b596cc 72%, var(--lav-edge) 100%);
  }
  .label__plant {
    position: absolute; left: 95px; top: 2px; width: 133px; height: 101px; border-radius: 50%;
    background: radial-gradient(ellipse at center, var(--plant-core) 0%, var(--plant-mid) 45%, rgba(0,0,0,0) 72%);
  }
  .label__band {
    position: absolute; left: 147px; top: 0; width: 35px; height: 100%;
    background: var(--band); box-sizing: border-box;
    border-left: 1px solid var(--gold); border-right: 1px solid var(--gold);
    color: var(--band-text, var(--white)); text-align: center; overflow: hidden;
  }
  .band__brand, .band__type, .band__pure, .band__volume {
    position: absolute; left: 0; width: 100%; display: block; text-align: center; white-space: nowrap; line-height: 1;
  }
  .band__brand { top: 5px; font-size: 7px; font-weight: 600; }
  .band__brand::before { content: ""; display: block; width: 7px; height: 7px; margin: 0 auto 2px; border: 1px solid currentColor; border-radius: 50%; }
  .band__type { top: 24px; font-size: 4.5px; font-weight: 600; }
  .band__pure { top: 42px; font-size: 4px; }
  .band__volume { bottom: 6px; font-size: 3.6px; }
  .label__name {
    position: absolute; left: 132px; top: 56px; width: 65px; height: 20px; box-sizing: border-box;
    background: var(--white); border: 1px solid var(--gold);
    font-family: var(--script); font-size: 13px; line-height: 19px; text-align: center; color: var(--ink); white-space: nowrap;
  }

  .dieline { position: absolute; left: 0; top: 0; }
</style>
</head>
<body>

<section class="label-sheet" aria-label="Bottle labels">
  <div class="label" style="left:253px;top:76px;--band:var(--eucalyptus);--plant-core:#5f7a3a;--plant-mid:#7fa055">
    <div class="label__plant" role="img" aria-label="Eucalyptus leaves and flowers"></div>
    <div class="label__band"><span class="band__brand">Sela Vale</span><span class="band__type">essential oil</span><span class="band__pure">100% pure</span><span class="band__volume">15ml - 0.50 fl.oz</span></div>
    <div class="label__name">Eucalyptus</div>
  </div>

  <div class="label" style="left:641px;top:73px;--band:var(--tea-tree);--plant-core:#6f9a3c;--plant-mid:#8bb55a">
    <div class="label__plant" role="img" aria-label="Tea tree leaves"></div>
    <div class="label__band"><span class="band__brand">Sela Vale</span><span class="band__type">essential oil</span><span class="band__pure">100% pure</span><span class="band__volume">15ml - 0.50 fl.oz</span></div>
    <div class="label__name">Tea Tree</div>
  </div>

  <div class="label" style="left:253px;top:218px;--band:var(--peppermint);--plant-core:#5d7c45;--plant-mid:#8a8fa8">
    <div class="label__plant" role="img" aria-label="Peppermint leaves and blossoms"></div>
    <div class="label__band"><span class="band__brand">Sela Vale</span><span class="band__type">essential oil</span><span class="band__pure">100% pure</span><span class="band__volume">15ml - 0.50 fl.oz</span></div>
    <div class="label__name">Peppermint</div>
  </div>

  <div class="label" style="left:641px;top:216px;--band:var(--oregano);--plant-core:#4f7a2c;--plant-mid:#78a34a">
    <div class="label__plant" role="img" aria-label="Oregano leaves"></div>
    <div class="label__band"><span class="band__brand">Sela Vale</span><span class="band__type">essential oil</span><span class="band__pure">100% pure</span><span class="band__volume">15ml - 0.50 fl.oz</span></div>
    <div class="label__name">Oregano</div>
  </div>

  <div class="label" style="left:253px;top:372px;--band:var(--lemon);--plant-core:#6b8a3e;--plant-mid:#b9b04a">
    <div class="label__plant" role="img" aria-label="Lemon branch with fruit and blossoms"></div>
    <div class="label__band"><span class="band__brand">Sela Vale</span><span class="band__type">essential oil</span><span class="band__pure">100% pure</span><span class="band__volume">15ml - 0.50 fl.oz</span></div>
    <div class="label__name">Lemon</div>
  </div>

  <div class="label label--lavender" style="left:641px;top:374px;--band:var(--lavender);--plant-core:#8f6bb5;--plant-mid:#b59ad0">
    <div class="label__plant" role="img" aria-label="Lavender blossoms"></div>
    <div class="label__band"><span class="band__brand">Sela Vale</span><span class="band__type">essential oil</span><span class="band__pure">100% pure</span><span class="band__volume">15ml - 0.50 fl.oz</span></div>
    <div class="label__name">Lavender</div>
  </div>
</section>

<svg class="dieline" width="1200" height="1000" viewBox="0 0 1200 1000" aria-label="Box dieline">
  <defs>
    <linearGradient id="side-left" x1="517" x2="620" y1="0" y2="0" gradientUnits="userSpaceOnUse">
      <stop offset="0" stop-color="#2f4420"/><stop offset="1" stop-color="#c2d19e"/>
    </linearGradient>
    <linearGradient id="side-right" x1="735" x2="888" y1="0" y2="0" gradientUnits="userSpaceOnUse">
      <stop offset="0" stop-color="#d3dfb0"/><stop offset="0.55" stop-color="#8fa86a"/><stop offset="1" stop-color="#2f4420"/>
    </linearGradient>
  </defs>

  <rect class="board" x="277" y="518" width="673" height="439" fill="var(--board)" stroke="#555" stroke-width="1"/>

  <g class="flaps" fill="var(--box-green)">
    <path d="M620,670 V560 L630,545 H775 L785,560 V670 Z"/>
    <path d="M517,670 V655 L545,592 H620 V670 Z"/>
    <path d="M785,670 V592 H860 L888,655 V670 Z"/>
    <path d="M620,803 V930 L630,945 H775 L785,930 V803 Z"/>
    <path d="M517,803 V818 L545,885 H620 V803 Z"/>
    <path d="M785,803 V885 H860 L888,818 V803 Z"/>
    <path d="M347,670 L340,678 V795 L347,803 Z"/>
  </g>

  <g class="body">
    <rect x="347" y="670" width="170" height="133" fill="var(--box-green)"/>
    <rect x="517" y="670" width="103" height="133" fill="url(#side-left)"/>
    <rect x="620" y="670" width="57" height="133" fill="var(--box-light)"/>
    <rect x="735" y="670" width="153" height="133" fill="url(#side-right)"/>
    <rect x="677" y="670" width="58" height="133" fill="var(--box-green)"/>
    <line x1="680" y1="670" x2="680" y2="803" stroke="var(--gold)" stroke-width="1.5"/>
    <line x1="732" y1="670" x2="732" y2="803" stroke="var(--gold)" stroke-width="1.5"/>
  </g>

  <g class="folds" stroke="#7f9a5f" stroke-width="0.6" fill="none">
    <line x1="517" y1="670" x2="517" y2="803"/>
    <line x1="620" y1="592" x2="620" y2="885"/>
    <line x1="785" y1="592" x2="785" y2="885"/>
    <line x1="517" y1="670" x2="888" y2="670"/>
    <line x1="517" y1="803" x2="888" y2="803"/>
    <line x1="620" y1="568" x2="785" y2="568"/>
    <line x1="620" y1="922" x2="785" y2="922"/>
  </g>

  <g class="front-panel" font-family="Crimson Text, Georgia, serif" fill="var(--white)" text-anchor="middle">
    <circle cx="706" cy="685" r="5" fill="none" stroke="var(--white)" stroke-width="1"/>
    <text x="706" y="703" font-size="10" font-weight="600">Sela Vale</text>
    <text x="706" y="711" font-size="4">essential oil</text>
    <text x="706" y="737" font-size="4">100% pure</text>
    <rect x="652" y="742" width="101" height="30" fill="var(--white)" stroke="var(--gold)" stroke-width="1.2"/>
    <text x="702" y="764" font-family="Pinyon Script, cursive" font-size="19" fill="var(--ink)">Essential Oil</text>
    <text x="706" y="792" font-size="4.5">15 ml - 0.50 fl.oz</text>
  </g>

  <g class="back-panel" font-family="Crimson Text, Georgia, serif" fill="var(--white)" font-size="4.2">
    <text x="363" y="693" font-weight="600">Recommended Use</text>
    <text x="363" y="707">Essential oils may be used aromatically or topically in</text>
    <text x="363" y="712">a variety of ways including diffusers, massage,</text>
    <text x="363" y="717">compresses, baths, scrubs, lotions and sprays.</text>
    <text x="363" y="727">Essential oils should be diluted with a carrier oil</text>
    <text x="363" y="732">such as sweet almond or jojoba before</text>
    <text x="363" y="737">applying topically.</text>
    <text x="363" y="774" font-weight="600">CAUTION</text>
    <text x="363" y="779">For Ext. Use only</text>
    <text x="363" y="791" font-size="4.6">Keep out of the reach of children.</text>
    <text x="463" y="676">The fresh, crisp aroma</text>
    <text x="463" y="681">of this pure essential oil</text>
    <text x="463" y="686">is clarifying,</text>
    <text x="463" y="691">energizing and</text>
    <text x="463" y="696">soothing.</text>
    <text x="463" y="707">Ingredients:</text>
    <text x="463" y="712">100% pure botanical</text>
    <text x="463" y="717">essential oil.</text>
    <text x="463" y="728">Benefits:</text>
    <text x="463" y="733">Supports calm and</text>
    <text x="463" y="738">clear, easy breathing</text>
    <text x="463" y="743">for relaxing.</text>
    <text x="463" y="770">How it Works:</text>
    <text x="463" y="775">Distilled from leaves,</text>
    <text x="463" y="780">stems and flowers.</text>
    <text x="463" y="785">Carefully sourced</text>
    <text x="463" y="790">and bottled with care.</text>
  </g>

  <g class="measures" stroke="var(--measure)" stroke-width="0.7" fill="none">
    <line x1="300" y1="670" x2="347" y2="670" stroke-dasharray="2 2"/>
    <line x1="300" y1="803" x2="347" y2="803" stroke-dasharray="2 2"/>
    <line x1="305" y1="670" x2="305" y2="803"/>
    <line x1="347" y1="803" x2="347" y2="912" stroke-dasharray="2 2"/>
    <line x1="517" y1="803" x2="517" y2="912" stroke-dasharray="2 2"/>
    <line x1="620" y1="885" x2="620" y2="912" stroke-dasharray="2 2"/>
    <line x1="347" y1="907" x2="620" y2="907"/>
  </g>
  <g font-family="Crimson Text, Georgia, serif" font-size="8" fill="var(--measure)" text-anchor="middle">
    <text x="297" y="736" transform="rotate(90 297 736)">8 cm</text>
    <text x="432" y="915">10 cm</text>
    <text x="568" y="915">6 cm</text>
  </g>
</svg>

</body>
</html>
```